Civic Viewing Studio SmartPhone

We are looking for a fresh new look for our famous Screen Sense Pocketdeck cards. These cards are used as a pedagogical device by teachers and students to help people critically analyze media messages.

Now that we are in the era of Zolara 7, we would like the Screen Sense Pocketdeck to look fresh and new. All the content stays the same, but graphic elements, color and overall design can be changed to look contemporary and modern.

Target Market(s)

Teenagers, young adults, secondary and college teachers

Industry/Entity Type

Education

Colors

Designer to choose colors to be used in the design.

Requirements
Must have
• All the content that is on the current card, with icons and text
Nice to have
• Fresh use of color
• More modern phone design like the smartphones people use today
Should not have
• ...too much black

```html
<!DOCTYPE html>
<html lang="en">
<head>
<meta charset="utf-8">
<title>Civic Viewing Studio – Screen Sense Pocketdeck</title>
<link href="https://fonts.googleapis.com/css2?family=Roboto:wght@400;500;700&display=swap" rel="stylesheet">
<style>
  :root{
    --teal:#1a9fb5;
    --green:#8cc63f;
    --orange:#f15a29;
    --yellow:#f2b81a;
    --ink:#1b1b1b;
    --grey:#8d8d8d;
    --panel:#f1f1f3;
    --line:#d9d9de;
    --white:#ffffff;
    --photo-sky:#c9dbe4;
    --photo-leaf:#9fb36a;
    --photo-warm:#d9a98a;
  }
  *{margin:0;padding:0;box-sizing:border-box}
  html,body{width:1200px;height:930px;overflow:hidden;background:var(--white)}
  body{font-family:"Roboto",Arial,sans-serif;position:relative}
  .backdrop,.photo,.trim-lines{position:absolute;left:0;top:0;width:1200px;height:930px}
  .trim-lines{pointer-events:none}

  .brand-panel{position:absolute;left:700px;top:31px;width:471px;height:235px;background:var(--white);
    display:flex;align-items:flex-end;justify-content:center;gap:12px;padding-bottom:28px}
  .brand-mark{width:16px;height:16px;background:var(--teal);margin-bottom:8px}
  .brand-name{font-size:40px;font-weight:500;color:var(--grey);line-height:1}

  .phone{position:absolute;left:74px;top:28px;width:432px;height:876px;border-radius:68px;
    background:var(--ink);border:3px solid #cfcfcf;box-shadow:0 0 0 2px var(--ink)}
  .screen{position:absolute;left:22px;top:22px;width:382px;height:826px;border-radius:46px;overflow:hidden;background:var(--white)}
  .screen-header{height:95px;background:var(--orange)}
  .notch{position:absolute;left:111px;top:22px;width:210px;height:34px;background:var(--ink);border-radius:0 0 24px 24px;z-index:2}
  .notch i{position:absolute;background:#2e2e2e;border-radius:50%}
  .speaker{position:absolute;left:80px;top:14px;width:52px;height:5px;border-radius:3px;background:#3a3a3a}

  .discuss{height:300px;padding:18px 24px 0}
  .discuss-title{text-align:center;color:var(--orange);font-weight:700;font-size:26px;letter-spacing:1px;
    padding-bottom:10px;border-bottom:3px solid var(--orange)}
  .prompt-list{list-style:none;display:grid;grid-template-columns:1fr 1fr;column-gap:14px;row-gap:12px;margin-top:20px}
  .prompt{display:flex;align-items:center;gap:10px;height:38px}
  .prompt svg{width:38px;height:38px;flex:none}
  .prompt span{font-size:14px;font-weight:500;color:var(--ink);line-height:1.1}

  .media{height:431px;background:var(--panel);padding:34px 22px 0}
  .channel-grid{list-style:none;display:grid;grid-template-columns:repeat(3,1fr);row-gap:18px}
  .channel{display:flex;flex-direction:column;align-items:center;gap:7px}
  .channel svg{width:54px;height:54px}
  .channel span{font-size:12px;color:#333;line-height:1}
</style>
</head>
<body>

<svg class="backdrop" viewBox="0 0 1200 930" aria-hidden="true">
  <rect width="1200" height="930" fill="var(--yellow)"/>
  <path d="M0 0 L160 0 C110 120 70 300 96 520 L0 560 Z" fill="var(--teal)"/>
  <path d="M150 0 L390 0 L380 22 C300 26 220 40 140 70 Z" fill="var(--green)"/>
  <path d="M370 0 L760 0 C650 90 560 180 515 265 C470 160 430 70 370 0 Z" fill="var(--orange)"/>
</svg>

<svg class="photo" viewBox="0 0 1200 930" role="img" aria-label="Photo of four students laughing together while looking at a laptop at an outdoor table">
  <defs>
    <linearGradient id="photoTone" x1="0" y1="0" x2="1" y2="1">
      <stop offset="0" stop-color="var(--photo-sky)"/>
      <stop offset="0.45" stop-color="var(--photo-leaf)"/>
      <stop offset="1" stop-color="var(--photo-warm)"/>
    </linearGradient>
  </defs>
  <path d="M745 0 L1200 0 L1200 930 L985 930 C720 810 535 620 530 430 C528 260 610 120 745 0 Z" fill="url(#photoTone)"/>
</svg>

<svg class="trim-lines" viewBox="0 0 1200 930" aria-hidden="true">
  <rect x="31" y="31" width="1138" height="870" fill="none" stroke="var(--teal)" stroke-width="1"/>
  <rect x="26" y="26" width="1148" height="878" fill="none" stroke="var(--orange)" stroke-width="1"/>
</svg>

<div class="brand-panel">
  <span class="brand-mark"></span>
  <span class="brand-name">Civic Viewing Studio</span>
</div>

<div class="phone">
  <div class="notch">
    <i style="left:28px;top:10px;width:14px;height:14px"></i>
    <i style="left:58px;top:14px;width:6px;height:6px"></i>
    <span class="speaker"></span>
    <i style="left:148px;top:12px;width:10px;height:10px;background:#1c2a4a"></i>
    <i style="left:172px;top:8px;width:18px;height:18px"></i>
  </div>
  <div class="screen">
    <div class="screen-header"></div>

    <section class="discuss">
      <h1 class="discuss-title">LET'S TALK IT OVER</h1>
      <ul class="prompt-list">
        <li class="prompt"><svg viewBox="0 0 38 38"><circle cx="19" cy="19" r="19" fill="var(--teal)"/><polyline points="11,20 17,26 28,13" fill="none" stroke="#fff" stroke-width="4" stroke-linecap="round" stroke-linejoin="round"/></svg><span>Is It Real?</span></li>
        <li class="prompt"><svg viewBox="0 0 38 38"><circle cx="19" cy="19" r="19" fill="var(--green)"/><text x="19" y="26" font-size="20" font-weight="700" text-anchor="middle" fill="#fff" font-family="Roboto,sans-serif">$</text></svg><span>Who Profits?</span></li>
        <li class="prompt"><svg viewBox="0 0 38 38"><circle cx="19" cy="19" r="19" fill="var(--yellow)"/><text x="19" y="27" font-size="22" font-weight="700" text-anchor="middle" fill="#fff" font-family="Roboto,sans-serif">?</text></svg><span>Missing Voices</span></li>
        <li class="prompt"><svg viewBox="0 0 38 38"><circle cx="19" cy="19" r="19" fill="var(--orange)"/><path d="M19 28 L10 19 A5 5 0 0 1 19 13 A5 5 0 0 1 28 19 Z" fill="#fff"/></svg><span>Whose Values?</span></li>
        <li class="prompt"><svg viewBox="0 0 38 38"><circle cx="19" cy="19" r="19" fill="var(--orange)"/><path d="M8 19 C14 11 24 11 30 19 C24 27 14 27 8 19 Z" fill="#fff"/><circle cx="19" cy="19" r="4" fill="var(--orange)"/></svg><span>Hidden Meaning</span></li>
        <li class="prompt"><svg viewBox="0 0 38 38"><circle cx="19" cy="19" r="19" fill="var(--yellow)"/><rect x="17" y="9" width="4" height="13" rx="2" fill="#fff"/><circle cx="19" cy="27" r="2.5" fill="#fff"/></svg><span>Fair Portrayal?</span></li>
        <li class="prompt"><svg viewBox="0 0 38 38"><circle cx="19" cy="19" r="19" fill="var(--green)"/><path d="M11 19 H27 M21 13 L27 19 L21 25" fill="none" stroke="#fff" stroke-width="3.5" stroke-linecap="round" stroke-linejoin="round"/></svg><span>Too Simple?</span></li>
        <li class="prompt"><svg viewBox="0 0 38 38"><circle cx="19" cy="19" r="19" fill="var(--teal)"/><rect x="12" y="10" width="14" height="18" rx="2" fill="none" stroke="#fff" stroke-width="2.5"/><path d="M15 16 H23 M15 21 H21" stroke="#fff" stroke-width="2"/></svg><span>Note It Down</span></li>
      </ul>
    </section>

    <section class="media">
      <ul class="channel-grid">
        <li class="channel"><svg viewBox="0 0 54 54"><circle cx="27" cy="27" r="26" fill="#fff" stroke="var(--line)"/><rect x="15" y="18" width="24" height="18" fill="none" stroke="var(--ink)" stroke-width="2.5"/><path d="M19 23 H35 M19 28 H35 M19 32 H29" stroke="var(--ink)" stroke-width="2"/></svg><span>Newspapers</span></li>
        <li class="channel"><svg viewBox="0 0 54 54"><circle cx="27" cy="27" r="26" fill="#fff" stroke="var(--line)"/><circle cx="27" cy="27" r="12" fill="none" stroke="var(--ink)" stroke-width="2.5"/><path d="M15 27 H39 M27 15 C21 21 21 33 27 39 C33 33 33 21 27 15" fill="none" stroke="var(--ink)" stroke-width="2"/></svg><span>Web</span></li>
        <li class="channel"><svg viewBox="0 0 54 54"><circle cx="27" cy="27" r="26" fill="#fff" stroke="var(--line)"/><rect x="14" y="17" width="26" height="18" rx="2" fill="none" stroke="var(--ink)" stroke-width="2.5"/><path d="M21 39 H33" stroke="var(--ink)" stroke-width="2.5"/></svg><span>Television</span></li>
        <li class="channel"><svg viewBox="0 0 54 54"><circle cx="27" cy="27" r="26" fill="#fff" stroke="var(--line)"/><rect x="15" y="19" width="18" height="16" rx="2" fill="none" stroke="var(--ink)" stroke-width="2.5"/><path d="M33 24 L40 20 V34 L33 30 Z" fill="var(--ink)"/></svg><span>Film</span></li>
        <li class="channel"><svg viewBox="0 0 54 54"><circle cx="27" cy="27" r="26" fill="#fff" stroke="var(--line)"/><rect x="17" y="17" width="8" height="8" rx="2" fill="var(--ink)"/><rect x="29" y="17" width="8" height="8" rx="2" fill="var(--ink)"/><rect x="17" y="29" width="8" height="8" rx="2" fill="var(--ink)"/><rect x="29" y="29" width="8" height="8" rx="2" fill="var(--ink)"/></svg><span>Mobile Apps</span></li>
        <li class="channel"><svg viewBox="0 0 54 54"><circle cx="27" cy="27" r="26" fill="#fff" stroke="var(--line)"/><rect x="22" y="14" width="10" height="17" rx="5" fill="none" stroke="var(--ink)" stroke-width="2.5"/><path d="M17 27 A10 10 0 0 0 37 27 M27 37 V41" fill="none" stroke="var(--ink)" stroke-width="2.5"/></svg><span>Audio Shows</span></li>
        <li class="channel"><svg viewBox="0 0 54 54"><circle cx="27" cy="27" r="26" fill="#fff" stroke="var(--line)"/><rect x="14" y="16" width="12" height="10" fill="none" stroke="var(--ink)" stroke-width="2"/><rect x="28" y="16" width="12" height="22" fill="none" stroke="var(--ink)" stroke-width="2"/><rect x="14" y="28" width="12" height="10" fill="none" stroke="var(--ink)" stroke-width="2"/></svg><span>Graphic Novels</span></li>
        <li class="channel"><svg viewBox="0 0 54 54"><circle cx="27" cy="27" r="26" fill="#fff" stroke="var(--line)"/><path d="M14 18 C19 16 23 16 27 19 C31 16 35 16 40 18 V37 C35 35 31 35 27 38 C23 35 19 35 14 37 Z M27 19 V38" fill="none" stroke="var(--ink)" stroke-width="2.2" stroke-linejoin="round"/></svg><span>Print</span></li>
        <li class="channel"><svg viewBox="0 0 54 54"><circle cx="27" cy="27" r="26" fill="#fff" stroke="var(--line)"/><path d="M24 35 V16 L36 14 V32" fill="none" stroke="var(--ink)" stroke-width="2.5"/><circle cx="21" cy="35" r="3.5" fill="var(--ink)"/><circle cx="33" cy="32" r="3.5" fill="var(--ink)"/></svg><span>Songs</span></li>
        <li class="channel"><svg viewBox="0 0 54 54"><circle cx="27" cy="27" r="26" fill="#fff" stroke="var(--line)"/><path d="M15 18 H39 M15 27 H39 M15 36 H31" stroke="var(--ink)" stroke-width="3" stroke-linecap="round"/></svg><span>Feeds</span></li>
        <li class="channel"><svg viewBox="0 0 54 54"><circle cx="27" cy="27" r="26" fill="#fff" stroke="var(--line)"/><rect x="13" y="20" width="28" height="15" rx="7.5" fill="none" stroke="var(--ink)" stroke-width="2.5"/><path d="M18 27.5 H24 M21 24.5 V30.5" stroke="var(--ink)" stroke-width="2"/><circle cx="34" cy="27.5" r="2" fill="var(--ink)"/></svg><span>Games</span></li>
        <li class="channel"><svg viewBox="0 0 54 54"><circle cx="27" cy="27" r="26" fill="#fff" stroke="var(--line)"/><path d="M34 17 A12 12 0 1 0 34 37 A9 9 0 1 1 34 17 Z" fill="var(--ink)"/></svg><span>Unplug</span></li>
      </ul>
    </section>
  </div>
</div>

</body>
</html>
```